Stationery Design Project for Nimbora, Chicago

Nimbora, a street parking application which helps car drivers find a street parking spot by offering an ideal path along which to look for parking. This path is calculated by our algorithm based on data (e.g. historical data, baseball games schedule, etc.). Along this path the driver will find a spot and will also save 70% of the search time. Customer we target is reg. between 21 and 45 yo.

We envision something young, fresh, bright and original. Slightly abstract maybe. It should represent the idea and elements of finding street parking in the city, e.g. car(s), parking spot, people, city, etc. (just ideas!).

Logo is attached.

Requirement:
- Business Cards (2 Sided Full Color CMYK)
- Letterhead (1 Sided Full Color CMYK)
- Envelope (1 Sided Full Color CMYK)
- Sticker (1 Sided Full Color CMYK), round with a 2inch diameter.

Reason: We're starting to get more and more designs and need more time to look into all of them. Very exciting!! Thanks to everybody!

Hi all, we're in the process of selecting our favs. Though choices!!! Really good submissions. Will keep you posted and sorry for the delay.

Target Market(s)

Car drivers and owners between 21 and 45

Industry/Entity Type

Parking

Requirements
Must have
• Sticker should be round and include company URL nimbora.com and the new logo which we will attach soon.
Should not have
• Should not be too serious or boring.

```html
<!DOCTYPE html>
<html lang="en">
<head>
<meta charset="utf-8">
<title>Nimbora Business Card</title>
<link rel="stylesheet" href="https://fonts.googleapis.com/css2?family=Courier+Prime:wght@400;700&display=swap">
<style>
  :root {
    --stage: #e8e5e1;
    --card: #ffffff;
    --card-edge: #d6d3cf;
    --brand-blue: #1f7ac4;
    --panel-black: #050505;
    --ink: #1d1d1d;
    --ink-soft: #555555;
    --white: #ffffff;
    --ring-grey: #cfcfcf;
  }
  * { margin: 0; padding: 0; box-sizing: border-box; }
  html, body {
    width: 1124px;
    height: 1200px;
    overflow: hidden;
    background: var(--stage);
    font-family: "Courier Prime", "Courier New", monospace;
  }
  .canvas {
    position: relative;
    width: 1124px;
    height: 1200px;
  }
  .card {
    position: absolute;
    left: 139px;
    width: 846px;
    height: 484px;
    background: var(--card);
    border: 1px solid var(--card-edge);
    border-radius: 32px;
    overflow: hidden;
  }
  .card-front { top: 90px; }
  .card-back { top: 620px; }

  /* Front */
  .brand-lockup {
    position: absolute;
    left: 46px;
    top: 190px;
    display: flex;
    align-items: center;
    gap: 14px;
  }
  .brand-dot {
    width: 104px;
    height: 104px;
    border-radius: 50%;
    background: var(--brand-blue);
  }
  .brand-name {
    font-weight: 700;
    font-size: 54px;
    color: var(--ink);
    letter-spacing: -1px;
  }
  .url-strip {
    position: absolute;
    left: 449px;
    top: 103px;
    width: 37px;
    height: 286px;
    background: var(--brand-blue);
  }
  .url-strip span {
    position: absolute;
    left: 50%;
    top: 50%;
    transform: translate(-50%, -50%) rotate(-90deg);
    white-space: nowrap;
    color: var(--white);
    font-weight: 700;
    font-size: 21px;
    letter-spacing: 1px;
  }
  .contact-panel {
    position: absolute;
    left: 491px;
    top: 103px;
    right: 0;
    height: 286px;
    background: var(--panel-black);
    color: var(--white);
    padding: 14px 0 0 27px;
  }
  .contact-name {
    font-weight: 700;
    font-size: 29px;
    line-height: 34px;
  }
  .contact-title {
    font-size: 24px;
    line-height: 32px;
    margin-bottom: 12px;
  }
  .contact-line {
    display: flex;
    align-items: center;
    gap: 4px;
    font-size: 24px;
    line-height: 32px;
  }
  .contact-line svg { width: 16px; height: 16px; fill: var(--white); flex: none; }
  .contact-address {
    margin-top: 16px;
    font-size: 24px;
    line-height: 33px;
  }

  /* Back */
  .back-mark {
    position: absolute;
    left: 50%;
    top: 40px;
    transform: translateX(-50%);
    width: 250px;
    height: 250px;
    border-radius: 50%;
    background: var(--brand-blue);
    box-shadow: 0 0 0 12px var(--white), 0 0 0 16px var(--ring-grey);
    display: flex;
    align-items: center;
    justify-content: center;
  }
  .back-mark span {
    color: var(--white);
    font-weight: 700;
    font-size: 46px;
  }
  .back-url {
    position: absolute;
    left: 0;
    right: 0;
    top: 372px;
    text-align: center;
    font-weight: 700;
    font-size: 40px;
    letter-spacing: 3px;
    color: var(--ink-soft);
  }
</style>
</head>
<body>
<main class="canvas">
  <section class="card card-front">
    <div class="brand-lockup">
      <div class="brand-dot"></div>
      <div class="brand-name">nimbora</div>
    </div>
    <div class="url-strip"><span>www.nimbora.com</span></div>
    <div class="contact-panel">
      <div class="contact-name">Your Name</div>
      <div class="contact-title">Title</div>
      <div class="contact-line">
        <svg viewBox="0 0 16 16" aria-hidden="true"><path d="M3 1h3l1.5 4-2 1.5a9 9 0 0 0 4 4l1.5-2 4 1.5v3a2 2 0 0 1-2 2A13 13 0 0 1 1 3a2 2 0 0 1 2-2z"/></svg>
        <span>123-456-789</span>
      </div>
      <div class="contact-line">
        <svg viewBox="0 0 16 16" aria-hidden="true"><path d="M5 1h6a1 1 0 0 1 1 1v12a1 1 0 0 1-1 1H5a1 1 0 0 1-1-1V2a1 1 0 0 1 1-1zm0 3v6h6V4z"/></svg>
        <span>123-456-789</span>
      </div>
      <div class="contact-line">
        <svg viewBox="0 0 16 16" aria-hidden="true"><path d="M1 4h14v9H1zm1 1 6 4 6-4z"/></svg>
        <span>info@nimbora.com</span>
      </div>
      <div class="contact-address">Complex name, Street<br>State, zip code</div>
    </div>
  </section>

  <section class="card card-back">
    <div class="back-mark"><span>nimbora</span></div>
    <div class="back-url">www.nimbora.com</div>
  </section>
</main>
</body>
</html>
```